Design a New Business Card for Our Company

We are looking for fresh, unique, and a modern business card that reflects our roots as digital marketing agency focused on SEM.

Industry/Entity Type

Marketing

Contact Information for Business Card

looking for very unique out of the box designs. clean and modern that compliments our logo

Requirements
Must have
• colors should match our logo
• Front should have name, address, email, and phone/fax of the person, phone/fax are the same number
• back should have our url

```html
<!DOCTYPE html>
<html lang="en">
<head>
<meta charset="utf-8">
<title>Brightpath Solutions – Business Card</title>
<link href="https://fonts.googleapis.com/css2?family=Open+Sans:wght@400;600;700;800&display=swap" rel="stylesheet">
<style>
  :root {
    --stage: #2b2b2b;
    --paper: #ffffff;
    --brand-blue: #5593cf;
    --brand-blue-deep: #4a86c2;
    --ink-grey: #8a8a8a;
    --rule-grey: #b5b5b5;
    --on-blue: #ffffff;
  }
  * { box-sizing: border-box; margin: 0; padding: 0; }
  html, body { width: 1200px; height: 907px; overflow: hidden; }
  body {
    background: var(--stage);
    font-family: "Open Sans", sans-serif;
    display: flex;
    align-items: center;
    justify-content: center;
    gap: 48px;
  }
  .card {
    position: relative;
    width: 540px;
    height: 309px;
    box-shadow: 0 10px 28px rgba(0,0,0,.45);
  }

  /* Front */
  .card-front { background: var(--paper); color: var(--ink-grey); }
  .brand {
    position: absolute;
    top: 34px;
    right: 36px;
    display: flex;
    align-items: center;
    gap: 10px;
  }
  .brand-dot {
    width: 22px; height: 22px;
    border-radius: 50%;
    background: var(--brand-blue);
  }
  .brand-name {
    font-weight: 700;
    font-size: 24px;
    color: var(--brand-blue);
    letter-spacing: -0.3px;
  }
  .rule {
    position: absolute;
    height: 1px;
    background: var(--rule-grey);
  }
  .rule-top { top: 88px; left: 200px; right: 36px; }
  .rule-bottom { top: 222px; left: 36px; width: 220px; }
  .company-address {
    position: absolute;
    top: 100px;
    right: 36px;
    text-align: right;
    font-size: 12px;
    line-height: 1.4;
  }
  .company-address .company-name { color: var(--brand-blue); font-weight: 600; }
  .person {
    position: absolute;
    top: 170px;
    left: 36px;
  }
  .person-name { font-size: 17px; font-weight: 700; color: var(--brand-blue); }
  .person-role { font-size: 12px; color: var(--ink-grey); margin-top: 1px; }
  .contact-list {
    position: absolute;
    top: 234px;
    left: 36px;
    list-style: none;
    font-size: 12px;
    line-height: 1;
  }
  .contact-list li {
    display: flex;
    align-items: center;
    gap: 7px;
    height: 16px;
  }
  .contact-icon { width: 13px; height: 13px; flex: none; }

  /* Back */
  .card-back {
    background: var(--brand-blue);
    color: var(--on-blue);
  }
  .back-brand {
    position: absolute;
    top: 50%;
    left: 50%;
    transform: translate(-50%, -60%);
    display: flex;
    align-items: center;
    gap: 12px;
  }
  .back-brand .brand-dot { width: 28px; height: 28px; background: var(--on-blue); }
  .back-brand .brand-name { font-size: 32px; color: var(--on-blue); }
  .back-url {
    position: absolute;
    bottom: 28px;
    left: 0; right: 0;
    text-align: center;
    font-size: 14px;
    letter-spacing: .2px;
  }
</style>
</head>
<body>

<section class="card card-front" aria-label="Card front">
  <div class="brand">
    <span class="brand-dot"></span>
    <span class="brand-name">Brightpath Solutions</span>
  </div>
  <div class="rule rule-top"></div>
  <address class="company-address" style="font-style:normal">
    <div class="company-name">Brightpath Solutions</div>
    <div>N. 8 Cedar Lane, Suite 200,</div>
    <div>Tacoma, WA 55555</div>
  </address>

  <div class="person">
    <div class="person-name">Dana Whitfield</div>
    <div class="person-role">Owner</div>
  </div>
  <div class="rule rule-bottom"></div>

  <ul class="contact-list">
    <li>
      <svg class="contact-icon" viewBox="0 0 14 14" aria-hidden="true"><circle cx="7" cy="7" r="7" fill="#5593cf"/><path d="M4.6 3.6l1.3 1.5-.7.9c.5 1 1.2 1.8 2.2 2.4l.9-.7 1.6 1.3-.6 1.3c-2.8-.4-5-2.6-5.4-5.4z" fill="#fff"/></svg>
      <span>555.010.2040</span>
    </li>
    <li>
      <svg class="contact-icon" viewBox="0 0 14 14" aria-hidden="true"><circle cx="7" cy="7" r="7" fill="#5593cf"/><rect x="4.5" y="3.5" width="5" height="2.5" fill="#fff"/><rect x="3.5" y="6.3" width="7" height="3" rx=".5" fill="#fff"/><rect x="4.8" y="8.6" width="4.4" height="2" fill="#fff" stroke="#5593cf" stroke-width=".5"/></svg>
      <span>555.010.2040</span>
    </li>
    <li>
      <svg class="contact-icon" viewBox="0 0 14 14" aria-hidden="true"><circle cx="7" cy="7" r="7" fill="#5593cf"/><rect x="3.5" y="4.5" width="7" height="5" fill="#fff"/><path d="M3.5 4.5L7 7.3l3.5-2.8" fill="none" stroke="#5593cf" stroke-width=".8"/></svg>
      <span>hello@brightpathsolutions.com</span>
    </li>
    <li>
      <svg class="contact-icon" viewBox="0 0 14 14" aria-hidden="true"><circle cx="7" cy="7" r="7" fill="#5593cf"/><g fill="none" stroke="#fff" stroke-width=".8"><circle cx="7" cy="7" r="3.6"/><ellipse cx="7" cy="7" rx="1.6" ry="3.6"/><path d="M3.4 7h7.2"/></g></svg>
      <span>www.brightpathsolutions.com</span>
    </li>
  </ul>
</section>

<section class="card card-back" aria-label="Card back">
  <div class="back-brand">
    <span class="brand-dot"></span>
    <span class="brand-name">Brightpath Solutions</span>
  </div>
  <div class="back-url">www.brightpathsolutions.com</div>
</section>

</body>
</html>
```